Business Card front and back

I am looking for business card design. I really really like the design file I uploaded named 627788_19250069_3478263_85f427ee_image

Target Market(s)

Corporate Fitness High end Private country club

Industry/Entity Type

Fitness Industry

Contact Information for Business Card

The last image I like as an example I uploaded a bunch of my logos. The file labeled "the signature" is my business card information for you to use

Colors
0054AA
0677BA
7BADD7
CADEEF
E8F1F8

Requirements
Must have
• E-mail sigThe file I uploaded labeled "627788_19250069_3478263_85f427ee_image" with all the plus signs on the back if those could be the logo symbol I uploaded labeled "1 back.png"

```html
<!DOCTYPE html>
<html lang="en">
<head>
<meta charset="utf-8">
<title>Peak Form Studio – Business Card</title>
<link href="https://fonts.googleapis.com/css2?family=Exo+2:wght@400;700;800&family=Ubuntu:wght@400;500&display=swap" rel="stylesheet">
<style>
  :root {
    --stage: #1c1c1d;
    --card: #2d2d2f;
    --card-deep: #232325;
    --blue: #4a82c9;
    --blue-soft: #7badd7;
    --white: #ffffff;
    --muted: #d9dadc;
  }
  * { box-sizing: border-box; margin: 0; padding: 0; }
  html, body {
    width: 1200px; height: 1015px; overflow: hidden;
    background: var(--stage);
  }
  .stage {
    position: relative; width: 1200px; height: 1015px;
    display: flex; flex-direction: column; align-items: center; justify-content: center; gap: 60px;
  }
  .card {
    position: relative; width: 700px; height: 400px; overflow: hidden;
    background: var(--card);
    box-shadow: 0 14px 40px rgba(0,0,0,.55);
  }

  /* ---------- back ---------- */
  .card-back__pattern {
    position: absolute; inset: 0;
    background: linear-gradient(200deg, #8a8a8c 0%, #4a4a4c 35%, #2d2d2f 60%, #0c0c0d 100%);
  }
  .card-back__brand {
    position: absolute; left: 50%; top: 50%; transform: translate(-50%, -50%);
    display: flex; align-items: center; gap: 14px;
    padding: 14px 22px; background: var(--card-deep);
  }

  /* ---------- brand lockup ---------- */
  .brand__mark { width: 26px; height: 26px; background: var(--blue); flex: none; }
  .brand__name {
    font-family: "Exo 2", sans-serif; font-weight: 800; font-size: 30px;
    letter-spacing: 1px; color: var(--white); text-transform: uppercase; white-space: nowrap;
  }

  /* ---------- front ---------- */
  .card-front__brand {
    position: absolute; left: 60px; top: 130px;
    display: flex; align-items: center; gap: 14px;
  }
  .contact {
    position: absolute; left: 90px; top: 240px;
    list-style: none; font-family: "Ubuntu", sans-serif; font-size: 17px; color: var(--white);
  }
  .contact__item { display: flex; align-items: center; gap: 12px; height: 30px; white-space: nowrap; }
  .contact__item svg { width: 18px; height: 18px; flex: none; fill: var(--blue); }

  .portrait {
    position: absolute; left: 440px; top: 34px; width: 220px; height: 188px;
    border: 2px solid var(--blue);
    background: radial-gradient(circle at 55% 45%, #8d7a6c 0%, #4c4644 38%, #262627 75%);
  }
  .person {
    position: absolute; right: 40px; top: 238px; text-align: right;
  }
  .person__name {
    font-family: "Exo 2", sans-serif; font-weight: 800; font-size: 28px;
    text-transform: uppercase; color: var(--white); letter-spacing: .5px; line-height: 1;
  }
  .person__name span { color: var(--blue); }
  .person__role {
    font-family: "Ubuntu", sans-serif; font-size: 17px; color: var(--white); margin-top: 4px;
  }
  .band { position: absolute; left: 0; bottom: 0; width: 700px; height: 76px; }
  .band polygon { fill: var(--blue); }
  .website {
    position: absolute; right: 40px; bottom: 18px;
    font-family: "Ubuntu", sans-serif; font-size: 16px; color: var(--white); letter-spacing: .3px;
  }
</style>
</head>
<body>
<main class="stage">

  <section class="card card-back">
    <div class="card-back__pattern" role="img" aria-label="Repeated brand symbols fading from light grey to black"></div>
    <div class="card-back__brand">
      <span class="brand__mark"></span>
      <span class="brand__name">Peak Form Studio</span>
    </div>
  </section>

  <section class="card card-front">
    <div class="card-front__brand">
      <span class="brand__mark"></span>
      <span class="brand__name">Peak Form Studio</span>
    </div>

    <ul class="contact">
      <li class="contact__item">
        <svg viewBox="0 0 24 24" aria-hidden="true"><path d="M6.6 10.8a15.1 15.1 0 0 0 6.6 6.6l2.2-2.2a1 1 0 0 1 1-.25 11.4 11.4 0 0 0 3.6.6 1 1 0 0 1 1 1V20a1 1 0 0 1-1 1A17 17 0 0 1 3 4a1 1 0 0 1 1-1h3.5a1 1 0 0 1 1 1c0 1.25.2 2.45.6 3.6a1 1 0 0 1-.25 1z"/></svg>
        555-014-2287
      </li>
      <li class="contact__item">
        <svg viewBox="0 0 24 24" aria-hidden="true"><path d="M2 5h20v14H2zm2 2v.4l8 5.2 8-5.2V7zm0 2.8V17h16V9.8l-8 5.2z"/></svg>
        dale@peakformstudio.co
      </li>
      <li class="contact__item">
        <svg viewBox="0 0 24 24" aria-hidden="true"><path d="M12 2a7 7 0 0 0-7 7c0 5.2 7 13 7 13s7-7.8 7-13a7 7 0 0 0-7-7zm0 9.5A2.5 2.5 0 1 1 12 6.5a2.5 2.5 0 0 1 0 5z"/></svg>
        Lakeview District
      </li>
    </ul>

    <div class="portrait" role="img" aria-label="Portrait photo of the consultant"></div>

    <div class="person">
      <p class="person__name">Dale <span>Marrow</span></p>
      <p class="person__role">Consultant</p>
    </div>

    <svg class="band" viewBox="0 0 700 76" aria-hidden="true">
      <polygon points="0,68 340,68 350,58 370,24 700,24 700,76 0,76"/>
    </svg>
    <p class="website">www.peakformstudio.com</p>
  </section>

</main>
</body>
</html>
```